High value cover design for an A4 ideation pad.

The product is NOT A BOOK.

It's an A4 ideation pad for professionals, designers and creators who handwrite their ideas. Visualise creators like Milo Varnet, Owen Plaskit and Gregor Lunwick in your mind's eye.

I'm looking for a cover design for the ideation pad. Both front and back.

It should look, feel and convey the following.

--> A handcrafted product experience

--> High value & Elegance

--> Inspiration

Mandatory --> See Uploaded Files --> Files 1, 5 & 6

Target Market(s)

- Designers

-Creative Professionals

- Entrepreneurs

who handwrite their ideas. Visualise creators like Milo Varnet, Owen Plaskit and Gregor Lunwick in your mind's eye.

Industry/Entity Type

Stationary

Font styles to use
Script
Other font styles liked:
• Calligraphy

Colors
fbed22

Requirements
Must have
• Title text - Quiet Kettle Notes

-Text in gold on brown leather background to convey high value for the front cover.

--> High value & Elegance

--> Inspiration

--> Should compel the customers to pick up and own the idea pad
Nice to have
• That's my take but other ideas are welcome
Should not have
• Must not convey

- low value

```html
<!DOCTYPE html>
<html lang="en">
<head>
<meta charset="utf-8">
<title>Quiet Kettle Notes – Pad Covers</title>
<link rel="stylesheet" href="https://fonts.googleapis.com/css2?family=Cinzel:wght@400;600&family=Pinyon+Script&display=swap">
<style>
  :root {
    --backdrop: #9d9d9d;
    --paper: #f3f3f1;
    --leather-light: #6b4428;
    --leather-dark: #3d2414;
    --gold: #c3942c;
    --gold-bright: #e2bd4e;
  }
  * { margin: 0; padding: 0; box-sizing: border-box; }
  html, body { width: 1200px; height: 764px; overflow: hidden; }
  body {
    position: relative;
    background: var(--backdrop);
    font-family: "Cinzel", "Times New Roman", serif;
    color: var(--gold);
  }
  .cover {
    position: absolute;
    top: 123px;
    width: 400px;
    height: 543px;
    background: var(--paper);
  }
  .cover--front {
    left: 95px;
    background: radial-gradient(ellipse at 45% 40%, var(--leather-light) 0%, #53331d 55%, var(--leather-dark) 100%);
  }
  .cover--back { left: 699px; }

  .frame {
    position: absolute;
    left: 20px; top: 22px;
    width: 359px; height: 484px;
  }
  .frame svg { display: block; }

  .ornament {
    position: absolute;
    background: linear-gradient(90deg, rgba(195,148,44,0.15), rgba(226,189,78,0.8), rgba(195,148,44,0.15));
    border-radius: 40% 40% 20% 20%;
  }
  .ornament--foot { left: 152px; top: 482px; width: 97px; height: 25px; }
  .ornament--crest { left: 160px; top: 322px; width: 80px; height: 22px; }

  .wordmark {
    position: absolute;
    left: 0; right: 0; top: 188px;
    text-align: center;
    font-family: "Pinyon Script", "Brush Script MT", cursive;
    font-weight: 400;
    color: var(--gold-bright);
  }
  .wordmark__top {
    display: block;
    font-size: 30px;
    line-height: 34px;
  }
  .wordmark__main {
    display: block;
    font-size: 88px;
    line-height: 86px;
  }
  .rule {
    position: absolute;
    left: 86px; top: 314px;
    width: 228px; height: 2px;
    background: var(--gold-bright);
  }
  .rule::before, .rule::after {
    content: "";
    position: absolute; top: -2px;
    width: 6px; height: 6px;
    background: var(--gold-bright);
    transform: rotate(45deg);
  }
  .rule::before { left: -3px; }
  .rule::after { right: -3px; }

  .imprint {
    position: absolute;
    left: 0; right: 0; top: 370px;
    text-align: center;
  }
  .imprint__name {
    font-size: 21px;
    font-weight: 600;
    letter-spacing: 0.1em;
  }
  .imprint__contacts {
    display: flex;
    justify-content: center;
    gap: 18px;
    margin-top: 14px;
    font-size: 12px;
    letter-spacing: 0.06em;
  }
  .contact { display: flex; align-items: center; gap: 5px; }
  .contact svg { flex: none; }
  .imprint__web {
    margin-top: 24px;
    font-size: 11px;
    letter-spacing: 0.42em;
    padding-left: 0.42em;
  }
</style>
</head>
<body>

  <section class="cover cover--front" aria-label="Front cover">
    <div class="frame">
      <svg width="359" height="484" viewBox="0 0 359 484" fill="none" stroke="#e2bd4e" stroke-width="1.5">
        <polyline points="120,483 1,483 1,1 358,1 358,483 237,483"/>
      </svg>
    </div>

    <h1 class="wordmark">
      <span class="wordmark__top">Quiet Kettle</span>
      <span class="wordmark__main">Notes</span>
    </h1>
    <div class="rule"></div>
    <div class="ornament ornament--crest" role="img" aria-label="Gold filigree flourish beneath the title"></div>
    <div class="ornament ornament--foot" role="img" aria-label="Gold filigree flourish set into the bottom of the frame"></div>
  </section>

  <section class="cover cover--back" aria-label="Back cover">
    <div class="frame">
      <svg width="359" height="484" viewBox="0 0 359 484" fill="none" stroke="#c3942c" stroke-width="1.5">
        <polyline points="120,483 1,483 1,1 358,1 358,483 237,483"/>
      </svg>
    </div>

    <div class="imprint">
      <p class="imprint__name">QUIET KETTLE NOTES</p>
      <div class="imprint__contacts">
        <span class="contact">
          <svg width="15" height="15" viewBox="0 0 16 16" aria-hidden="true">
            <rect width="16" height="16" rx="3" fill="#c3942c"/>
            <path d="M5 3.5l1.6 2.2-1 1.2c.6 1.3 1.6 2.3 2.9 2.9l1.2-1 2.2 1.6-.8 1.8c-3.8-.2-7.1-3.5-7.3-7.3z" fill="#f3f3f1"/>
          </svg>
          55501 23987
        </span>
        <span class="contact">
          <svg width="15" height="15" viewBox="0 0 16 16" aria-hidden="true">
            <rect width="16" height="16" rx="3" fill="#c3942c"/>
            <rect x="3.5" y="4.5" width="9" height="7" rx="1" fill="none" stroke="#f3f3f1" stroke-width="1.3"/>
            <polyline points="3.8,5 8,8.5 12.2,5" fill="none" stroke="#f3f3f1" stroke-width="1.3"/>
          </svg>
          QUIETKETTLENOTES@MAIL
        </span>
      </div>
      <p class="imprint__web">WWW.QUIETKETTLENOTES.COM</p>
    </div>

    <div class="ornament ornament--foot" role="img" aria-label="Gold filigree flourish set into the bottom of the frame"></div>
  </section>

</body>
</html>
```